School Website

I need a design for a School (2 sections: Primary 6-12 years and Secondary 12-18 years). The first page is just a choice of the 2 sections. After we'll need 2 websites (with the same structure: Menu, ...) but with different colors. In fact, we need for end of October, 6 design of school website. So the best websites are going to be made available to you in the future (in pixelharbor) but privately.

Target Market(s)

Public, Parents, ...

Coding

Coded - Design and coding required

Number of Pages Required

5+ page

Font styles to use
Sans Serif

Colors
34a6d7
85cae6
cee9f5
ffffff

Requirements
Must have
• You can check the old Website: http: / /velmot.be We need the same pages with the same content. Menu: - HomePage - News and communication (like blog page) - Activities (like blog page, with photo gallery) - Contact (Contact form + maps) - In the main menu, we need a special button to connect to an external Website ( button needs to be different than the other menu items The name of this button is "Parents Area"). The logo of 2 sections are attached. Please use it for the design and the choice of colors.
Nice to have
• This is a web design of other school that we like: https://www.quintelo.be

```html
<!DOCTYPE html>
<html lang="en">
<head>
<meta charset="utf-8">
<title>Athénée Royal de Velmot</title>
<link href="https://fonts.googleapis.com/css2?family=Poppins:wght@300;400;500;600;700;800&display=swap" rel="stylesheet">
<style>
:root{
  --yellow:#eea723;
  --yellow-dark:#e39a12;
  --navy:#0a4585;
  --blue:#0d6fb8;
  --sky:#4cc3ec;
  --ink:#1d1d1d;
  --text:#444;
  --footer:#242424;
  --white:#fff;
}
*{margin:0;padding:0;box-sizing:border-box}
html,body{width:1200px;height:3743px;overflow:hidden}
body{position:relative;font-family:'Poppins',sans-serif;color:var(--text);background:var(--white)}
.abs{position:absolute}
/* header */
.header{left:0;top:0;width:1200px;height:99px;background:var(--white);border-bottom:1px solid #eee}
.brand{left:90px;top:24px;display:flex;align-items:center;gap:10px;font-weight:800;font-size:20px;color:var(--navy);line-height:1.05}
.brand .mark{width:18px;height:18px;border-radius:50%;background:var(--yellow)}
.nav{left:0;top:43px;font-size:13px;font-weight:400;color:#222}
.nav a{position:absolute;white-space:nowrap;text-decoration:none;color:#222}
.nav a.active{color:var(--yellow)}
/* skewed buttons: sky offset shape behind a solid face */
.btn-skew{display:block;text-align:center;font-weight:600;text-decoration:none;isolation:isolate}
.btn-skew::before{content:"";position:absolute;inset:8px -5px -8px 5px;background:var(--sky);transform:skew(-6deg);z-index:0}
.btn-skew span{display:block;position:relative;z-index:1;width:100%;height:100%}
.nav-cta{left:966px;top:29px;width:141px;height:42px;font-size:13px;line-height:42px}
.nav-cta span{background:var(--yellow);color:var(--white)}
/* hero */
.hero{left:0;top:99px;width:1200px;height:546px;background:var(--yellow);overflow:hidden}
.hero .blob{left:360px;top:155px;width:210px;height:210px;border-radius:50%;background:rgba(255,255,255,.1)}
.hero .slant{left:-200px;top:300px;width:900px;height:400px;background:rgba(255,255,255,.05);transform:rotate(-20deg)}
.hero-kicker{left:89px;top:182px;font-size:37px;font-weight:600;color:var(--white)}
.hero-title{left:89px;top:230px;font-size:48px;font-weight:800;color:var(--white);letter-spacing:-1px;white-space:nowrap;z-index:2}
.hero-sub{left:89px;top:296px;font-size:20px;font-weight:400;color:var(--white)}
.hero-btn{left:93px;top:344px;width:139px;height:40px;font-size:13px;line-height:40px}
.hero-btn span{background:var(--white);color:var(--yellow)}
.hero-photo{left:640px;top:32px;width:377px;height:514px;background:linear-gradient(180deg,#f3c56a 0%,#d7542f 55%,#2f6f93 100%);border-radius:190px 190px 0 0}
.hero-deco{left:0;top:0}
/* section headings */
.sec-title{left:0;width:1200px;text-align:center;font-weight:700;color:var(--ink);font-size:44px;letter-spacing:1px}
.divider{left:550px;width:100px;height:14px}
.lead{left:270px;width:660px;text-align:center;font-size:14px;line-height:25px;color:#333}
/* cards */
.card{width:313px;height:319px;background:var(--white);box-shadow:0 4px 24px rgba(0,0,0,.09);overflow:hidden}
.card .icon{position:absolute;left:26px;top:47px;width:78px;height:78px;border-radius:50%;display:flex;align-items:center;justify-content:center}
.card h3{position:absolute;left:26px;top:148px;font-size:19px;font-weight:600;color:var(--ink)}
.card p{position:absolute;left:26px;top:185px;font-size:12.5px;line-height:21px;color:#333}
.card .go{position:absolute;right:-14px;bottom:-14px;width:58px;height:58px;border-radius:50%;background:#eee;display:flex;align-items:flex-start;justify-content:flex-start;padding:16px 0 0 16px}
.card .go.on{background:var(--sky)}
/* rules band */
.rules{left:0;top:1376px;width:1200px;height:411px;background:var(--navy)}
.rules-title{left:0;top:1450px;width:1200px;text-align:center;font-size:46px;font-weight:700;color:var(--white)}
.rule-item{display:flex;gap:12px;align-items:center;color:var(--white);font-size:14px;line-height:21px}
.rule-item a{color:var(--yellow);font-weight:600;text-decoration:underline}
.ring{border-radius:50%;background:var(--blue);display:flex;align-items:center;justify-content:center}
.ring .ph{border-radius:50%;background:linear-gradient(160deg,#cfe3ee,#8fb1c7 60%,#e0a46a)}
.dot-blue{border-radius:50%;background:var(--blue)}
/* gallery */
.tile{overflow:hidden}
.tile .ph{position:absolute;inset:0}
.tile .shade{position:absolute;inset:0;background:linear-gradient(180deg,rgba(0,0,0,0) 50%,rgba(0,0,0,.55))}
.tile .tag{position:absolute;left:15px;top:15px;width:40px;height:40px;border-radius:50%;background:var(--navy);display:flex;align-items:center;justify-content:center}
.tile .name{position:absolute;left:0;width:100%;text-align:center;font-size:22px;font-weight:700;color:var(--white)}
/* meals */
.meals-photo{left:0;top:2467px;width:513px;height:436px;background:linear-gradient(135deg,#7fae3c,#c7371f 45%,#d99a3a 75%,#e8e2d6)}
.chat{left:440px;top:2422px;width:120px;height:120px;border-radius:50%;background:var(--blue);display:flex;align-items:center;justify-content:center}
.meals-title{left:606px;top:2567px;font-size:44px;font-weight:700;color:var(--ink);letter-spacing:1px}
.meals-text{left:607px;top:2662px;width:480px;font-size:13.5px;line-height:27px;color:#222}
.arrow-btn{width:38px;height:38px;border-radius:50%;display:flex;align-items:center;justify-content:center}
/* contact */
.footer-bg{left:0;top:3361px;width:1200px;height:382px;background:var(--footer)}
.form{left:275px;top:3114px;width:650px;height:383px;background:var(--white);box-shadow:0 6px 30px rgba(0,0,0,.08)}
.field{border:1px solid #e2e2e2;background:var(--white);font-size:12px;color:#666;padding:14px 11px}
.submit{left:526px;top:3417px;width:145px;height:40px;font-size:13px;line-height:40px}
.submit span{background:var(--yellow);color:var(--white)}
.info{display:flex;gap:20px;align-items:flex-start;color:var(--white)}
.info .ic{width:76px;height:76px;border-radius:50%;background:var(--yellow);border:5px solid #3a3a3a;flex:none;display:flex;align-items:center;justify-content:center;margin-top:-12px}
.info h4{font-size:16px;font-weight:600;margin-bottom:4px}
.info p{font-size:13px;line-height:22px}
.foot-line{left:87px;top:3701px;width:1023px;height:1px;background:#444}
.copy{left:87px;top:3714px;font-size:12.5px;color:var(--white)}
.sitemap{left:1049px;top:3714px;font-size:12.5px;color:var(--yellow);text-decoration:underline}
.top-btn{left:1136px;top:3661px;width:38px;height:38px;border-radius:50%;background:var(--yellow);display:flex;align-items:center;justify-content:center}
</style>
</head>
<body>

<header class="abs header">
  <div class="abs brand"><span class="mark"></span><span>ATHÉNÉE<br>ROYAL DE VELMOT</span></div>
  <nav class="abs nav">
    <a class="active" style="left:431px">HOME</a>
    <a style="left:516px">NEWS &amp; COMMUNICATION</a>
    <a style="left:740px">ACIVITIES</a>
    <a style="left:846px">CONTACT</a>
  </nav>
  <a class="abs btn-skew nav-cta"><span>PARENTS AREA</span></a>
</header>

<section class="abs hero">
  <div class="abs slant"></div>
  <div class="abs blob"></div>
  <div class="abs hero-photo" role="img" aria-label="Smiling schoolgirl in a red shirt wearing a blue backpack"></div>
  <div class="abs hero-kicker">ATHÉNÉE</div>
  <div class="abs hero-title">ROYAL DE VELMOT</div>
  <div class="abs hero-sub">MATERNELLES ET PRIMAIRES</div>
  <a class="abs btn-skew hero-btn"><span>PARENTS AREA</span></a>
  <svg class="abs hero-deco" width="1200" height="546" aria-hidden="true">
    <path d="M676 39v14M669 46h14" stroke="#fff" stroke-width="2.5"/>
    <circle cx="840" cy="57" r="8" fill="none" stroke="#fff" stroke-width="2"/>
    <circle cx="913" cy="186" r="8" fill="none" stroke="#fff" stroke-width="2"/>
    <path d="M611 240l-9 14h18z" fill="none" stroke="#fff" stroke-width="2"/>
  </svg>
</section>

<h2 class="abs sec-title" style="top:718px">ROYAL DE VELMOT</h2>
<svg class="abs divider" style="top:779px" viewBox="0 0 100 14" aria-hidden="true">
  <line x1="8" y1="7" x2="38" y2="7" stroke="var(--yellow)"/><line x1="62" y1="7" x2="92" y2="7" stroke="var(--yellow)"/>
  <circle cx="5" cy="7" r="3" fill="var(--yellow)"/><circle cx="95" cy="7" r="3" fill="var(--yellow)"/>
  <circle cx="50" cy="7" r="6" fill="none" stroke="var(--yellow)" stroke-width="1.5"/><circle cx="50" cy="7" r="3" fill="var(--yellow)"/>
</svg>
<p class="abs lead" style="top:803px">Lorem ipsum dolor sit amet, consectetur adipiscing elit, sed do eiusmod tempor incididunt ut labore et dolore magna aliqua. Quis ipsum suspendisse ultrices gravida. Risus commodo viverra maecenas accumsan lacus vel facilisis.</p>

<article class="abs card" style="left:89px;top:933px">
  <div class="icon" style="background:var(--yellow)"><svg width="40" height="40" viewBox="0 0 40 40" fill="none" stroke="#fff" stroke-width="1.8"><circle cx="14" cy="13" r="6"/><circle cx="26" cy="13" r="6"/><path d="M3 33c0-7 5-11 11-11s11 4 11 11zM22 22c1-.3 2-.5 4-.5 6 0 11 4 11 11h-12"/></svg></div>
  <h3>Our Teaching Team</h3>
  <p>Director of the fundamental section<br>Rue des Tilleuls, 12 - 4820 Velmot<br>081 / 47.36.12<br>Mrs Claire VANDERLEY</p>
  <div class="go"><svg width="18" height="12" viewBox="0 0 18 12" fill="none" stroke="#333" stroke-width="1.5"><path d="M1 6h15M11 1l5 5-5 5"/></svg></div>
</article>
<article class="abs card" style="left:443px;top:933px">
  <div class="icon" style="background:var(--sky)"><svg width="40" height="40" viewBox="0 0 40 40" fill="none" stroke="#fff" stroke-width="1.8"><rect x="5" y="8" width="28" height="24" rx="2"/><path d="M5 15h28M12 5v6M26 5v6"/><circle cx="30" cy="30" r="6" fill="var(--sky)"/><path d="M27 30l2 2 4-4"/></svg></div>
  <h3>Our schedules &amp; daycare</h3>
  <p>Director of the fundamental section<br>Rue des Tilleuls, 12 - 4820 Velmot<br>081 / 47.36.12<br>Mrs Claire VANDERLEY</p>
  <div class="go on"><svg width="18" height="12" viewBox="0 0 18 12" fill="none" stroke="#fff" stroke-width="1.5"><path d="M1 6h15M11 1l5 5-5 5"/></svg></div>
</article>
<article class="abs card" style="left:795px;top:933px">
  <div class="icon" style="background:var(--navy)"><svg width="40" height="40" viewBox="0 0 40 40" fill="none" stroke="#fff" stroke-width="1.6"><path d="M20 4v6M20 4h6v3h-6M8 18l12-8 12 8M6 18h28v16H6zM17 34v-7h6v7M10 22h4v4h-4zM26 22h4v4h-4z"/></svg></div>
  <h3>School Holidays</h3>
  <p>Director of the fundamental section<br>Rue des Tilleuls, 12 - 4820 Velmot<br>081 / 47.36.12<br>Mrs Claire VANDERLEY</p>
  <div class="go"><svg width="18" height="12" viewBox="0 0 18 12" fill="none" stroke="#333" stroke-width="1.5"><path d="M1 6h15M11 1l5 5-5 5"/></svg></div>
</article>

<section class="abs rules"></section>
<div class="abs dot-blue" style="left:-48px;top:1597px;width:96px;height:96px"></div>
<div class="abs ring" style="left:157px;top:1429px;width:130px;height:130px"><div class="ph" style="width:98px;height:98px" role="img" aria-label="Two children studying together at a desk"></div></div>
<div class="abs ring" style="left:940px;top:1426px;width:162px;height:162px"><div class="ph" style="width:120px;height:120px" role="img" aria-label="Smiling boy wearing glasses"></div></div>
<div class="abs ring" style="left:798px;top:1603px;width:116px;height:116px"><div class="ph" style="width:88px;height:88px" role="img" aria-label="Child reading with a book on his head"></div></div>
<h2 class="abs rules-title">Rules of Procedure</h2>
<svg class="abs divider" style="top:1511px" viewBox="0 0 100 14" aria-hidden="true">
  <line x1="8" y1="7" x2="38" y2="7" stroke="#fff"/><line x1="62" y1="7" x2="92" y2="7" stroke="#fff"/>
  <circle cx="5" cy="7" r="3" fill="#fff"/><circle cx="95" cy="7" r="3" fill="#fff"/>
  <circle cx="50" cy="7" r="6" fill="none" stroke="#fff" stroke-width="1.5"/><circle cx="50" cy="7" r="3" fill="#fff"/>
</svg>
<div class="abs rule-item" style="left:402px;top:1543px">
  <svg width="40" height="50" viewBox="0 0 40 50" fill="none" stroke="#fff" stroke-width="1.5"><rect x="10" y="4" width="26" height="34"/><rect x="4" y="12" width="26" height="34" fill="var(--navy)"/><path d="M9 20h16M9 26h16M9 32h16M9 38h10"/></svg>
  <div>Please find attached the rules of procedure<br><a>Rules of Procedure</a></div>
</div>
<div class="abs rule-item" style="left:395px;top:1620px">
  <svg width="46" height="44" viewBox="0 0 46 44" fill="none" stroke="#fff" stroke-width="1.5"><path d="M3 6l18 4v30L3 36zM43 6l-18 4v30l18-4zM7 16l10 2M7 22l10 2M29 18l10-2M29 24l10-2"/></svg>
  <div>Please find attached the educational Project<br><a>Educational Project</a></div>
</div>
<div class="abs ring" style="left:173px;top:1647px;width:230px;height:230px"><div class="ph" style="width:172px;height:172px" role="img" aria-label="Smiling schoolgirl with a backpack"></div></div>
<div class="abs dot-blue" style="left:1042px;top:1736px;width:96px;height:96px"></div>

<h2 class="abs sec-title" style="top:1904px">ROYAL DE VELMOT ACTIVITIES</h2>
<svg class="abs divider" style="top:1966px" viewBox="0 0 100 14" aria-hidden="true">
  <line x1="8" y1="7" x2="38" y2="7" stroke="var(--yellow)"/><line x1="62" y1="7" x2="92" y2="7" stroke="var(--yellow)"/>
  <circle cx="5" cy="7" r="3" fill="var(--yellow)"/><circle cx="95" cy="7" r="3" fill="var(--yellow)"/>
  <circle cx="50" cy="7" r="6" fill="none" stroke="var(--yellow)" stroke-width="1.5"/><circle cx="50" cy="7" r="3" fill="var(--yellow)"/>
</svg>
<p class="abs lead" style="top:1990px">Lorem ipsum dolor sit amet, consectetur adipiscing elit, sed do eiusmod tempor incididunt ut labore et dolore magna aliqua. Quis ipsum suspendisse ultrices gravida. Risus commodo viverra maecenas accumsan lacus vel facilisis.</p>

<div class="abs tile" style="left:148px;top:2103px;width:301px;height:261px">
  <div class="ph" role="img" aria-label="Child climbing on a colourful playground" style="background:linear-gradient(135deg,#c98a3c,#d8463a 40%,#6c8fb8 70%,#8a6a45)"></div>
  <div class="shade"></div>
  <div class="tag"><svg width="22" height="22" viewBox="0 0 22 22" fill="none" stroke="#fff" stroke-width="1.4"><path d="M2 20V9l9-6 9 6v11M6 20v-7h10v7M11 3v17"/></svg></div>
  <div class="name" style="top:212px">Playground</div>
</div>
<div class="abs tile" style="left:449px;top:2103px;width:302px;height:261px">
  <div class="ph" role="img" aria-label="Children raising their hands in sunlight" style="background:linear-gradient(135deg,#f5e4a0,#8a9a55 45%,#4a4032)"></div>
  <div class="shade"></div>
  <div class="tag"><svg width="22" height="22" viewBox="0 0 22 22" fill="none" stroke="#fff" stroke-width="1.4"><circle cx="7" cy="5" r="2.5"/><circle cx="15" cy="5" r="2.5"/><path d="M3 20v-8l4-3 4 3 4-3 4 3v8"/></svg></div>
  <div class="name" style="top:212px">Picnic</div>
</div>
<div class="abs tile" style="left:751px;top:2088px;width:301px;height:291px">
  <div class="ph" role="img" aria-label="Little girl in a floral dress in a classroom" style="background:linear-gradient(160deg,#e9e6e6,#b9b4b8 50%,#6e6a73)"></div>
  <div class="shade"></div>
  <div class="tag" style="background:var(--yellow)"><svg width="22" height="22" viewBox="0 0 22 22" fill="none" stroke="#fff" stroke-width="1.4"><circle cx="11" cy="7" r="4"/><path d="M4 20c0-5 3-8 7-8s7 3 7 8"/></svg></div>
  <div class="name" style="top:243px">Events</div>
</div>

<div class="abs meals-photo" role="img" aria-label="Table of colourful Mexican dishes with guacamole, tomatoes and limes"></div>
<div class="abs chat"><svg width="60" height="50" viewBox="0 0 60 50" fill="none" stroke="#fff" stroke-width="2.5"><path d="M8 6h38a6 6 0 0 1 6 6v18a6 6 0 0 1-6 6H24l-12 10v-10H8a6 6 0 0 1-6-6V12a6 6 0 0 1 6-6z"/><circle cx="17" cy="21" r="3" fill="#fff"/><circle cx="27" cy="21" r="3" fill="#fff"/><circle cx="37" cy="21" r="3" fill="#fff"/></svg></div>
<h2 class="abs meals-title">MEALS OFFERED</h2>
<svg class="abs divider" style="left:688px;top:2630px" viewBox="0 0 100 14" aria-hidden="true">
  <line x1="8" y1="7" x2="38" y2="7" stroke="var(--yellow)"/><line x1="62" y1="7" x2="92" y2="7" stroke="var(--yellow)"/>
  <circle cx="5" cy="7" r="3" fill="var(--yellow)"/><circle cx="95" cy="7" r="3" fill="var(--yellow)"/>
  <circle cx="50" cy="7" r="6" fill="none" stroke="var(--yellow)" stroke-width="1.5"/><circle cx="50" cy="7" r="3" fill="var(--yellow)"/>
</svg>
<p class="abs meals-text">to the children&nbsp; of the nursery section of L'ATHÉNÉE ROYAL DE VELMOT during the whole school year!<br><br>Pilot project for your little ones, our little ones&nbsp; of the AR VELMOT. Which team !</p>
<div class="abs arrow-btn" style="left:1024px;top:2842px;background:#e8e8e8"><svg width="16" height="12" viewBox="0 0 16 12" fill="none" stroke="#333" stroke-width="1.5"><path d="M15 6H2M6 1L1 6l5 5"/></svg></div>
<div class="abs arrow-btn" style="left:1072px;top:2842px;background:var(--yellow)"><svg width="16" height="12" viewBox="0 0 16 12" fill="none" stroke="#fff" stroke-width="1.5"><path d="M1 6h13M10 1l5 5-5 5"/></svg></div>

<h2 class="abs sec-title" style="top:3007px">CONTACT US</h2>
<svg class="abs divider" style="top:3069px" viewBox="0 0 100 14" aria-hidden="true">
  <line x1="8" y1="7" x2="38" y2="7" stroke="var(--yellow)"/><line x1="62" y1="7" x2="92" y2="7" stroke="var(--yellow)"/>
  <circle cx="5" cy="7" r="3" fill="var(--yellow)"/><circle cx="95" cy="7" r="3" fill="var(--yellow)"/>
  <circle cx="50" cy="7" r="6" fill="none" stroke="var(--yellow)" stroke-width="1.5"/><circle cx="50" cy="7" r="3" fill="var(--yellow)"/>
</svg>

<div class="abs footer-bg"></div>
<div class="abs form"></div>
<div class="abs field" style="left:321px;top:3137px;width:267px;height:44px">Name</div>
<div class="abs field" style="left:609px;top:3137px;width:267px;height:44px">Email Address</div>
<div class="abs field" style="left:321px;top:3200px;width:267px;height:43px">Phone Number</div>
<div class="abs field" style="left:609px;top:3200px;width:267px;height:43px">Address</div>
<div class="abs field" style="left:321px;top:3263px;width:555px;height:127px;padding-top:10px">Message</div>
<a class="abs btn-skew submit"><span>SUBSCRIBE</span></a>

<div class="abs info" style="left:131px;top:3573px">
  <div class="ic"><svg width="22" height="28" viewBox="0 0 22 28" fill="#fff"><path d="M11 0a10 10 0 0 0-10 10c0 8 10 18 10 18s10-10 10-18A10 10 0 0 0 11 0zm0 14a4 4 0 1 1 0-8 4 4 0 0 1 0 8z"/></svg></div>
  <div><h4>LOCATION:</h4><p>RUE DES TILLEULS 12 / A, 4820<br>VELMOT, BELGIUM</p></div>
</div>
<div class="abs info" style="left:529px;top:3573px">
  <div class="ic"><svg width="28" height="28" viewBox="0 0 28 28" fill="none" stroke="#fff" stroke-width="2"><circle cx="14" cy="14" r="12"/><path d="M14 7v7l-4 4"/></svg></div>
  <div><h4>SCHEDULE:</h4><p>MONDAY TO FRIDAY<br>7 AM - 6 PM</p></div>
</div>
<div class="abs info" style="left:844px;top:3573px">
  <div class="ic"><svg width="26" height="26" viewBox="0 0 24 24" fill="#fff"><path d="M6.6 10.8a15 15 0 0 0 6.6 6.6l2.2-2.2a1 1 0 0 1 1-.25 11.4 11.4 0 0 0 3.6.57 1 1 0 0 1 1 1V20a1 1 0 0 1-1 1A17 17 0 0 1 3 4a1 1 0 0 1 1-1h3.5a1 1 0 0 1 1 1c0 1.25.2 2.45.57 3.57a1 1 0 0 1-.25 1z"/></svg></div>
  <div><h4>PHONE:</h4><p>+32 81 47 36 12</p></div>
</div>
<div class="abs top-btn"><svg width="12" height="16" viewBox="0 0 12 16" fill="none" stroke="#fff" stroke-width="1.5"><path d="M6 15V2M1 6l5-5 5 5"/></svg></div>
<div class="abs foot-line"></div>
<div class="abs copy">© 2019 ROYAL DE VELMOT.ALL RIGHTS RESERVED</div>
<a class="abs sitemap">SITE MAP</a>

</body>
</html>
```